furniture and home contents restoration

I need to list the services that we perform in our studio.
we serve the general public as well as the insurance/ remediation industry

```html
<!DOCTYPE html>
<html lang="en">
<head>
<meta charset="utf-8">
<title>Keystone Refinishers – Business Card</title>
<link rel="stylesheet" href="https://fonts.googleapis.com/css2?family=Source+Sans+3:wght@400;600;700&display=swap">
<style>
  :root {
    --navy: #1b2a33;
    --paper: #e6e6ea;
    --band: #8a8c93;
    --muted: #797c84;
    --ink-light: #dfe3e7;
    --bg: #d9dadd;
  }
  * { box-sizing: border-box; margin: 0; padding: 0; }
  html, body { width: 1200px; height: 1000px; overflow: hidden; }
  body {
    background: var(--bg);
    font-family: "Source Sans 3", sans-serif;
    position: relative;
  }
  .card {
    position: absolute;
    left: 250px;
    width: 700px;
    height: 400px;
    overflow: hidden;
    box-shadow: 0 4px 18px rgba(0,0,0,0.18);
  }
  /* Back: services list */
  .card-back { top: 60px; background: var(--navy); color: var(--ink-light); padding: 34px 44px; }
  .services-title { font-weight: 700; font-size: 19px; color: #f2f4f6; }
  .services-sub { font-size: 17px; margin-top: 2px; }
  .services-rule { border: 0; border-top: 1px solid #c9ced3; margin: 14px 0 14px; }
  .services { display: flex; gap: 30px; }
  .services ul { list-style: none; flex: 1; }
  .services li {
    font-size: 15.5px; line-height: 22px;
    display: flex; align-items: center; gap: 8px;
  }
  .services li svg { flex: none; }

  /* Front: identity */
  .card-front { top: 540px; background: var(--paper); }
  .wave { position: absolute; inset: 0; }
  .brand {
    position: absolute; left: 58px; top: 112px;
    font-weight: 700; font-size: 46px; line-height: 44px;
    color: var(--navy);
  }
  .tagline-top {
    position: absolute; left: 468px; top: 52px;
    font-weight: 700; font-size: 22px; line-height: 24px;
    color: var(--muted);
  }
  .person {
    position: absolute; left: 58px; top: 292px;
    font-weight: 700; font-size: 18px; letter-spacing: 0.5px;
    color: #e3e6e9;
  }
  .served {
    position: absolute; left: 58px; top: 330px;
    font-size: 15px; line-height: 19px; color: #d4d8dc;
  }
  .contact {
    position: absolute; left: 470px; top: 226px;
    font-size: 14.5px; line-height: 19px; color: #dfe3e7;
  }
  .contact .address { margin-bottom: 10px; }
  .contact ul { list-style: none; }
  .contact li { display: flex; align-items: center; gap: 8px; }
</style>
</head>
<body>

<section class="card card-back" aria-label="Services">
  <p class="services-title">On-Site Inspections and Desk Review Services</p>
  <p class="services-sub">Assessment Reports and Estimates for Repair and Restoration</p>
  <hr class="services-rule">
  <div class="services">
    <ul>
      <li><svg width="12" height="10" viewBox="0 0 12 10"><path d="M0 5h9M6 1l4 4-4 4" stroke="#c9ced3" stroke-width="1.4" fill="none"/></svg>Antique Repair and Restoration</li>
      <li><svg width="12" height="10" viewBox="0 0 12 10"><path d="M0 5h9M6 1l4 4-4 4" stroke="#c9ced3" stroke-width="1.4" fill="none"/></svg>Art Cleaning and Remounting</li>
      <li><svg width="12" height="10" viewBox="0 0 12 10"><path d="M0 5h9M6 1l4 4-4 4" stroke="#c9ced3" stroke-width="1.4" fill="none"/></svg>Art and Mirror Frame Repair</li>
      <li><svg width="12" height="10" viewBox="0 0 12 10"><path d="M0 5h9M6 1l4 4-4 4" stroke="#c9ced3" stroke-width="1.4" fill="none"/></svg>Chandelier Cleaning and Restoration</li>
      <li><svg width="12" height="10" viewBox="0 0 12 10"><path d="M0 5h9M6 1l4 4-4 4" stroke="#c9ced3" stroke-width="1.4" fill="none"/></svg>Document Restoration</li>
      <li><svg width="12" height="10" viewBox="0 0 12 10"><path d="M0 5h9M6 1l4 4-4 4" stroke="#c9ced3" stroke-width="1.4" fill="none"/></svg>Glass, Ceramic and Mirror Repair</li>
      <li><svg width="12" height="10" viewBox="0 0 12 10"><path d="M0 5h9M6 1l4 4-4 4" stroke="#c9ced3" stroke-width="1.4" fill="none"/></svg>Hardware Repair and Restoration</li>
      <li><svg width="12" height="10" viewBox="0 0 12 10"><path d="M0 5h9M6 1l4 4-4 4" stroke="#c9ced3" stroke-width="1.4" fill="none"/></svg>Kitchen Removal and Reinstallation</li>
      <li><svg width="12" height="10" viewBox="0 0 12 10"><path d="M0 5h9M6 1l4 4-4 4" stroke="#c9ced3" stroke-width="1.4" fill="none"/></svg>Lamp Cleaning and Restoration</li>
      <li><svg width="12" height="10" viewBox="0 0 12 10"><path d="M0 5h9M6 1l4 4-4 4" stroke="#c9ced3" stroke-width="1.4" fill="none"/></svg>Lamp Shade Replacement</li>
    </ul>
    <ul>
      <li><svg width="12" height="10" viewBox="0 0 12 10"><path d="M0 5h9M6 1l4 4-4 4" stroke="#c9ced3" stroke-width="1.4" fill="none"/></svg>Metal Polishing and Restoration</li>
      <li><svg width="12" height="10" viewBox="0 0 12 10"><path d="M0 5h9M6 1l4 4-4 4" stroke="#c9ced3" stroke-width="1.4" fill="none"/></svg>Odor Removal and Ozone Services</li>
      <li><svg width="12" height="10" viewBox="0 0 12 10"><path d="M0 5h9M6 1l4 4-4 4" stroke="#c9ced3" stroke-width="1.4" fill="none"/></svg>Photo Restoration</li>
      <li><svg width="12" height="10" viewBox="0 0 12 10"><path d="M0 5h9M6 1l4 4-4 4" stroke="#c9ced3" stroke-width="1.4" fill="none"/></svg>Upholstery Cleaning and Deodorizing</li>
      <li><svg width="12" height="10" viewBox="0 0 12 10"><path d="M0 5h9M6 1l4 4-4 4" stroke="#c9ced3" stroke-width="1.4" fill="none"/></svg>In-House Upholstery and Reupholstery</li>
      <li><svg width="12" height="10" viewBox="0 0 12 10"><path d="M0 5h9M6 1l4 4-4 4" stroke="#c9ced3" stroke-width="1.4" fill="none"/></svg>Rug Cleaning and Restoration</li>
      <li><svg width="12" height="10" viewBox="0 0 12 10"><path d="M0 5h9M6 1l4 4-4 4" stroke="#c9ced3" stroke-width="1.4" fill="none"/></svg>Musical Instrument Restoration</li>
      <li><svg width="12" height="10" viewBox="0 0 12 10"><path d="M0 5h9M6 1l4 4-4 4" stroke="#c9ced3" stroke-width="1.4" fill="none"/></svg>Window Treatment Repair/ Restoration</li>
      <li><svg width="12" height="10" viewBox="0 0 12 10"><path d="M0 5h9M6 1l4 4-4 4" stroke="#c9ced3" stroke-width="1.4" fill="none"/></svg>Leather Restoration and Replacement</li>
      <li><svg width="12" height="10" viewBox="0 0 12 10"><path d="M0 5h9M6 1l4 4-4 4" stroke="#c9ced3" stroke-width="1.4" fill="none"/></svg>Piano Restoration and Repair</li>
    </ul>
  </div>
</section>

<section class="card card-front" aria-label="Contact card">
  <svg class="wave" viewBox="0 0 700 400" preserveAspectRatio="none" aria-hidden="true">
    <path d="M0 232 C200 228 320 232 400 190 C480 150 570 150 700 146 L700 400 L0 400 Z" fill="var(--band)"/>
    <path d="M0 256 C200 252 330 256 410 214 C490 174 580 174 700 170 L700 400 L0 400 Z" fill="var(--navy)"/>
  </svg>
  <h1 class="brand">KEYSTONE<br>Refinishers</h1>
  <p class="tagline-top">Home Contents<br>Restoration</p>
  <p class="person">DANIEL MORETTI</p>
  <p class="served">Serving The General Public and<br>The Insurance Industry for Over 40 Years</p>
  <div class="contact">
    <p class="address">128 Orchard Hill Rd.<br>Riverton, NY 10599</p>
    <ul>
      <li><svg width="11" height="11" viewBox="0 0 12 12"><path d="M2 1l2.5 0 1 3-1.5 1c.7 1.4 1.6 2.3 3 3l1-1.5 3 1V11c-5 0-9-4-9-10z" fill="#dfe3e7"/></svg>555.014.2200</li>
      <li><svg width="11" height="11" viewBox="0 0 12 12"><rect x="3" y="0.5" width="6" height="11" rx="1" stroke="#dfe3e7" fill="none"/><circle cx="6" cy="9.5" r=".7" fill="#dfe3e7"/></svg>555.016.7391</li>
      <li><svg width="11" height="11" viewBox="0 0 12 12"><rect x="3" y="0.5" width="6" height="4" fill="#dfe3e7"/><rect x="0.5" y="5" width="11" height="5" fill="#dfe3e7"/><rect x="3" y="8" width="6" height="3.5" fill="#dfe3e7" stroke="#1b2a33" stroke-width=".6"/></svg>555.014.2260</li>
      <li><svg width="11" height="11" viewBox="0 0 12 12"><rect x="0.5" y="2.5" width="11" height="7" fill="#dfe3e7"/><path d="M0.5 2.5l5.5 4 5.5-4" stroke="#1b2a33" fill="none"/></svg>studio@keystonerefinish.com</li>
    </ul>
  </div>
</section>

</body>
</html>
```